Buch-/eBook-Cover für Traumatherapeutin
Zielgruppe
Ich bin Traumatherapeutin und schreibe ein Buch zum Thema Trauma bearbeiten.
Meine Zielgruppe sucht Heilung, Genesung, Selbstliebe etc.
Aufgabenstellung
Buchcover
Bitte erstell mir ein modernes positives inspirierendes Buchcover mit dem
Titel: 'Morgenlicht NEU entdecken“
Untertitel: „Spüre den Mut der ganz in dir wohnt“
Dr. Mira Kessow
Ich hätte gerne ein modernes Buch, das entweder einen Bezug zum Thema Trauma hat oder aber einfach stylische Schriftzüge. Bin aber auch offen für andere Vorschläge.
Dunkelblau, weiß und türkis oder auch rosa mag ich ganz gerne. Wobei Dunkelblau, weiß und türkis meine Favoriten sind und mit rosa höchstens kleinere Akzente gesetzt werden sollten.
Das Buchcover soll modern sein und direkt ansprechen. Gerne eine originelle Lösung, oder etwas Besonderes, etwas das Tiefe ausdrückt, oder man mehrmals hinsehen muss um etwas zu erkennen oder etwas das mehr Interpretationsspielraum lässt.
Gerne auch viel weiß, zumindest heller und nicht zu dunkel. Stylish, aber nicht überfrachtet.
Schreib mich gerne an, wenn du Fragen hast.
Ich habe mal zwei Beispiel von Typolösungen angehängt, die ich ganz cool fände.
Ich freue mich auf deine Ideen :-)
Ganz liebe Grüße
Mira

```html
<!DOCTYPE html>
<html lang="de">
<head>
<meta charset="utf-8">
<title>Morgenlicht NEU entdecken – Dr. Mira Kessow</title>
<link rel="stylesheet" href="https://fonts.googleapis.com/css2?family=Montserrat:wght@800&family=Source+Sans+3:wght@400;500&family=Dancing+Script:wght@700&family=Allura&display=swap">
<style>
  :root {
    --sky-light: #f4fafd;
    --sky-mid: #d6ecf4;
    --sky-edge: #b4dcea;
    --band-blue: #2f87b1;
    --title-blue: #7ab7d8;
    --script-navy: #15679a;
    --subtitle-navy: #17608f;
    --accent-teal: #6cb3c3;
    --wave-deep: #7fc6dc;
    --wave-pale: #d9f0f6;
    --white: #ffffff;
  }
  * { margin: 0; padding: 0; box-sizing: border-box; }
  html, body { width: 846px; height: 1200px; overflow: hidden; }
  body { background: var(--sky-light); }
  .cover {
    position: relative;
    width: 846px;
    height: 1200px;
    overflow: hidden;
    background: radial-gradient(ellipse 60% 45% at 45% 50%, var(--white) 0%, var(--sky-mid) 70%, var(--sky-edge) 100%);
  }
  .cover__backdrop { position: absolute; inset: 0; width: 846px; height: 1200px; }
  .author-band {
    position: absolute;
    left: 0; top: 161px;
    width: 846px; height: 53px;
    background: var(--band-blue);
    opacity: 0.95;
    display: flex; align-items: center; justify-content: center;
  }
  .author-band__name {
    font-family: "Source Sans 3", "Open Sans", sans-serif;
    font-weight: 500;
    font-size: 36px;
    letter-spacing: 0.5px;
    color: var(--white);
    padding-left: 0;
    margin-left: 0;
    line-height: 1;
  }
  .title {
    position: absolute;
    left: 0; top: 325px;
    width: 846px;
    text-align: center;
  }
  .title__block {
    display: block;
    font-family: "Montserrat", sans-serif;
    font-weight: 800;
    font-size: 90px;
    line-height: 1;
    color: var(--title-blue);
    letter-spacing: -1px;
  }
  .title__script {
    display: block;
    font-family: "Dancing Script", cursive;
    font-weight: 700;
    font-size: 150px;
    line-height: 1;
    color: var(--script-navy);
    margin: 8px 0 4px;
  }
  .subtitle {
    position: absolute;
    left: 344px; top: 860px;
    font-family: "Source Sans 3", "Open Sans", sans-serif;
    font-weight: 400;
    font-size: 34px;
    line-height: 1.2;
    color: var(--subtitle-navy);
  }
  .subtitle__line { display: block; white-space: nowrap; }
  .subtitle__line--second { padding-left: 17px; margin-top: 4px; }
  .subtitle__accent {
    font-family: "Allura", cursive;
    font-size: 62px;
    color: var(--accent-teal);
    line-height: 0.8;
    margin-left: 4px;
  }
</style>
</head>
<body>
  <main class="cover">
    <svg class="cover__backdrop" viewBox="0 0 846 1200" xmlns="http://www.w3.org/2000/svg">
      <defs>
        <linearGradient id="wave-top" x1="0" y1="0" x2="1" y2="1">
          <stop offset="0" stop-color="var(--wave-pale)"/>
          <stop offset="0.5" stop-color="var(--wave-deep)"/>
          <stop offset="1" stop-color="var(--wave-pale)"/>
        </linearGradient>
        <linearGradient id="wave-bottom" x1="0" y1="0" x2="1" y2="1">
          <stop offset="0" stop-color="var(--wave-deep)"/>
          <stop offset="0.55" stop-color="var(--wave-pale)"/>
          <stop offset="1" stop-color="var(--wave-deep)"/>
        </linearGradient>
      </defs>
      <g role="img" aria-label="Abstrakte türkisfarbene Wellenform in der oberen rechten Ecke">
        <path d="M451 0 C470 70 500 140 545 215 C600 290 700 345 846 370 L846 0 Z" fill="url(#wave-top)" opacity="0.85"/>
        <path d="M451 0 C470 70 500 140 545 215 C600 290 700 345 846 370" fill="none" stroke="var(--white)" stroke-width="3" stroke-dasharray="1 5" stroke-linecap="round"/>
      </g>
      <g role="img" aria-label="Abstrakte türkisfarbene Wellenform in der unteren linken Ecke">
        <path d="M0 784 C120 780 230 840 310 930 C380 1010 430 1100 462 1200 L0 1200 Z" fill="url(#wave-bottom)" opacity="0.85"/>
        <path d="M0 784 C120 780 230 840 310 930 C380 1010 430 1100 462 1200" fill="none" stroke="var(--white)" stroke-width="3" stroke-dasharray="1 5" stroke-linecap="round"/>
      </g>
    </svg>

    <header class="author-band">
      <span class="author-band__name">DR. MIRA KESSOW</span>
    </header>

    <h1 class="title">
      <span class="title__block">MORGENLICHT</span>
      <span class="title__script">NEU</span>
      <span class="title__block">ENTDECKEN</span>
    </h1>

    <p class="subtitle">
      <span class="subtitle__line">Spüre den <span class="subtitle__accent">Mut</span></span>
      <span class="subtitle__line subtitle__line--second">der ganz in dir wohnt!</span>
    </p>
  </main>
</body>
</html>
```